Velmora Consulting Business

** Please add the content information from my old business card
1. I would like to see a two sided business card with both options with the 1st Option--Tallow Spire-new WHITE BACKGROUND LOGO
2 nd Option-Tallow Spire - new BLACK- Background Logo
3rd -Option a business card with my Photo on the card
Please add the new word to the card information:
EXECUTION
AS THE OWNER'S REP
WE AIM TO ACHIEVE YOUR
INFRASTRUCTURE VISION with
OUR SPECIALIZATION & EXECUTION in:

FUNDING Planning
BUSINESS Planning
INFRASTRUCTURE Planning
PROJECT Management
Since 2012
_____________________________________________________________________
I want to get spot uv raised printing. I was liking a a nice rich white linen paper stock with black writing & NOT A COLORED CARD other than a variety of white or black cards concept

```html
<!DOCTYPE html>
<html lang="en">
<head>
<meta charset="utf-8">
<title>Velmora Consulting – Business Cards</title>
<link href="https://fonts.googleapis.com/css2?family=Open+Sans:wght@400;600;700&display=swap" rel="stylesheet">
<style>
  :root {
    --backdrop: #b9b9b9;
    --card-black: #231f20;
    --card-white: #f7f7f9;
    --ink-black: #1d1b1c;
    --ink-white: #ffffff;
    --accent-red: #e3173e;
    --decor-light: #e9e9ee;
    --decor-lighter: #fbfbfd;
  }
  * { box-sizing: border-box; margin: 0; padding: 0; }
  html, body { width: 1200px; height: 900px; overflow: hidden; }
  body {
    background: var(--backdrop);
    font-family: "Open Sans", Arial, sans-serif;
    position: relative;
  }
  .card {
    position: absolute;
    left: 240px;
    width: 720px;
    height: 411px;
    border-radius: 34px;
    overflow: hidden;
  }
  .card--back { top: 30px; background: var(--card-black); color: var(--ink-white); }
  .card--front { top: 459px; background: var(--card-white); color: var(--ink-black); }

  /* Back side */
  .back-content {
    position: absolute; inset: 0;
    display: flex; flex-direction: column; align-items: center; justify-content: center;
    text-align: center;
  }
  .wordmark {
    display: flex; align-items: center; gap: 10px;
    font-weight: 700; line-height: 1;
  }
  .wordmark__mark { width: 16px; height: 16px; background: var(--accent-red); }
  .card--back .wordmark { font-size: 48px; color: var(--ink-white); margin-bottom: 30px; }
  .mission { font-size: 17px; line-height: 1.3; letter-spacing: 0.2px; text-transform: none; }
  .mission + .mission { margin-top: 12px; }
  .since { margin-top: 8px; font-size: 17px; color: var(--accent-red); }

  /* Front side */
  .front-decor {
    position: absolute; right: 0; top: 0; width: 360px; height: 411px;
    background: linear-gradient(135deg, var(--decor-light) 0%, var(--decor-lighter) 70%);
  }
  .front-identity { position: absolute; left: 48px; top: 70px; }
  .card--front .wordmark { font-size: 44px; color: var(--ink-black); margin-bottom: 34px; }
  .person-name { font-size: 27px; font-weight: 600; color: var(--accent-red); line-height: 1.15; }
  .person-title { font-size: 17px; text-transform: uppercase; margin-top: 2px; }
  .contacts { list-style: none; margin-top: 24px; }
  .contacts li { display: flex; align-items: center; gap: 12px; font-size: 20px; line-height: 1.45; }
  .contacts svg { width: 20px; height: 20px; flex: none; }
  .locations {
    position: absolute; right: 36px; bottom: 34px;
    font-size: 19px; color: var(--ink-black);
  }
  .locations .dot { color: var(--accent-red); padding: 0 6px; }
</style>
</head>
<body>

<section class="card card--back" aria-label="Card back">
  <div class="back-content">
    <div class="wordmark"><span>Velmora Consulting</span><span class="wordmark__mark"></span></div>
    <p class="mission">EXECUTION AS THE OWNER'S REP<br>WE AIM TO ACHIEVE YOUR INFRASTRUCTURE VISION with<br>OUR SPECIALIZATION &amp; EXECUTION in:</p>
    <p class="mission">FUNDING Planning &nbsp; BUSINESS Planning<br>INFRASTRUCTURE Planning PROJECT Management</p>
    <p class="since">Since 2012</p>
  </div>
</section>

<section class="card card--front" aria-label="Card front">
  <div class="front-decor" role="img" aria-label="Soft raised spot UV decoration area"></div>
  <div class="front-identity">
    <div class="wordmark"><span>Velmora Consulting</span><span class="wordmark__mark"></span></div>
    <p class="person-name">Marisol Okafor-Brennan</p>
    <p class="person-title">CEO / Lead Project Manager</p>
    <ul class="contacts">
      <li>
        <svg viewBox="0 0 24 24" aria-hidden="true"><path d="M6.6 10.8a15.1 15.1 0 0 0 6.6 6.6l2.2-2.2a1 1 0 0 1 1-.25 11.4 11.4 0 0 0 3.6.57 1 1 0 0 1 1 1V20a1 1 0 0 1-1 1A17 17 0 0 1 3 4a1 1 0 0 1 1-1h3.5a1 1 0 0 1 1 1c0 1.25.2 2.45.57 3.57a1 1 0 0 1-.25 1z" fill="var(--ink-black)"/></svg>
        555.201.7734
      </li>
      <li>
        <svg viewBox="0 0 24 24" aria-hidden="true"><rect x="2" y="5" width="20" height="14" fill="var(--ink-black)"/><path d="M2 5l10 8 10-8" fill="none" stroke="var(--card-white)" stroke-width="1.6"/></svg>
        marisol@velmora.ca
      </li>
      <li>
        <svg viewBox="0 0 24 24" aria-hidden="true"><g fill="none" stroke="var(--ink-black)" stroke-width="1.8"><circle cx="12" cy="12" r="9.5"/><ellipse cx="12" cy="12" rx="4" ry="9.5"/><path d="M2.5 12h19M4 7h16M4 17h16"/></g></svg>
        www.velmora.ca
      </li>
    </ul>
  </div>
  <p class="locations">Northgate NT<span class="dot">•</span>Harlow NB</p>
</section>

</body>
</html>
```